Business Card Design for a Software Startup

We'd like to have a business card design. We already have a logo. Basically what we need is a clean design with name, address, cellphone and phone numbers, e-mail and web site address (front) and a space on the back with our logo with the company name on the right side and some texts on the bottom.
We are a development and consulting company in Brazil with highly qualified team of professionals in Java, iOS and Android development and consulting.

Target Market(s)

CIO, IT managers of mid to big size companies

Industry/Entity Type

Business

```html
<!DOCTYPE html>
<html lang="en">
<head>
<meta charset="utf-8">
<title>Vextra Business Card</title>
<link rel="stylesheet" href="https://fonts.googleapis.com/css2?family=Montserrat:wght@700&family=Questrial&display=swap">
<style>
  :root {
    --page: #eceef1;
    --navy: #1c3f6e;
    --navy-deep: #12325a;
    --card-blue: #1d4e82;
    --band-top: #1a4f86;
    --band-bottom: #173e6b;
    --accent-line: #3ea6dd;
    --ink: #1c3f6e;
    --grey: #555b63;
    --white: #ffffff;
  }
  * { margin: 0; padding: 0; box-sizing: border-box; }
  html, body { width: 1200px; height: 720px; overflow: hidden; }
  body { background: var(--page); position: relative; font-family: "Questrial", "Century Gothic", sans-serif; }

  .card {
    position: absolute;
    width: 525px;
    height: 300px;
    overflow: hidden;
    box-shadow: 0 6px 18px rgba(0,0,0,0.18);
  }

  /* Contact side */
  .card-front { left: 50px; top: 140px; background: var(--white); }
  .side-band {
    position: absolute; left: 0; top: 0; bottom: 0; width: 84px;
    background: linear-gradient(180deg, var(--band-top), var(--band-bottom));
  }
  .accent-line {
    position: absolute; left: 90px; top: 0; bottom: 0; width: 2px;
    background: var(--accent-line);
  }
  .brand-mark {
    position: absolute; left: 44px; top: 40px; width: 80px; height: 80px;
    background: var(--navy); border-radius: 10px; border: 3px solid var(--white);
  }
  .brand-name {
    position: absolute; left: 136px; top: 34px;
    font-family: "Montserrat", sans-serif; font-weight: 700;
    font-size: 56px; letter-spacing: 1px; color: var(--navy); line-height: 1;
  }
  .person {
    position: absolute; left: 112px; top: 122px;
    font-family: "Montserrat", sans-serif; font-weight: 700;
    font-size: 18px; color: var(--navy);
    text-decoration: underline; text-underline-offset: 3px;
  }
  .person .title { font-family: "Questrial", sans-serif; font-weight: 400; font-size: 14px; }
  .contact-list { position: absolute; left: 112px; top: 154px; list-style: none; }
  .contact-list li {
    display: flex; align-items: center; gap: 7px;
    font-size: 14px; color: var(--grey); line-height: 19px;
  }
  .contact-list svg { width: 11px; height: 11px; fill: var(--navy-deep); flex: none; }
  .address {
    position: absolute; left: 112px; top: 238px;
    font-size: 13.5px; color: var(--grey); line-height: 18px;
  }

  /* Brand side */
  .card-back {
    left: 625px; top: 280px;
    background: radial-gradient(ellipse at 50% 45%, #235a92 0%, var(--card-blue) 55%, #174373 100%);
  }
  .faint-square {
    position: absolute; left: 165px; top: 38px; width: 200px; height: 200px;
    border-radius: 26px; background: rgba(255,255,255,0.09);
  }
  .back-name {
    position: absolute; left: 0; right: 0; top: 100px; text-align: center;
    font-family: "Montserrat", sans-serif; font-weight: 700;
    font-size: 70px; letter-spacing: 2px; color: var(--white); line-height: 1;
  }
  .back-web {
    position: absolute; left: 0; right: 0; top: 246px; text-align: center;
    font-family: "Montserrat", sans-serif; font-weight: 700;
    font-size: 15px; letter-spacing: 5px; color: var(--white);
  }
</style>
</head>
<body>

  <section class="card card-front" aria-label="Contact side of business card">
    <div class="side-band"></div>
    <div class="accent-line"></div>
    <div class="brand-mark"></div>
    <div class="brand-name">VEXTRA</div>
    <div class="person">Your Name, <span class="title">Title</span></div>
    <ul class="contact-list">
      <li>
        <svg viewBox="0 0 24 24" aria-hidden="true"><path d="M6.6 10.8a15.1 15.1 0 0 0 6.6 6.6l2.2-2.2a1 1 0 0 1 1-.25 11.4 11.4 0 0 0 3.6.57 1 1 0 0 1 1 1V20a1 1 0 0 1-1 1A17 17 0 0 1 3 4a1 1 0 0 1 1-1h3.5a1 1 0 0 1 1 1c0 1.25.2 2.45.57 3.57a1 1 0 0 1-.25 1z"/></svg>
        123-456-7890
      </li>
      <li>
        <svg viewBox="0 0 24 24" aria-hidden="true"><path d="M7 1h10a2 2 0 0 1 2 2v18a2 2 0 0 1-2 2H7a2 2 0 0 1-2-2V3a2 2 0 0 1 2-2zm0 3v14h10V4zm5 15.5a1.2 1.2 0 1 0 0 2.4 1.2 1.2 0 0 0 0-2.4z"/></svg>
        456-085-4321
      </li>
      <li>
        <svg viewBox="0 0 24 24" aria-hidden="true"><path d="M2 5h20v14H2zm2 2v.5l8 5 8-5V7l-8 5z"/></svg>
        yourname@vextra.com
      </li>
      <li>
        <svg viewBox="0 0 24 24" aria-hidden="true"><path d="M12 2a10 10 0 1 0 0 20 10 10 0 0 0 0-20zm6.9 9h-3a15 15 0 0 0-1.3-5.6A8 8 0 0 1 18.9 11zM12 4.1c.9 1.3 1.7 3.6 1.9 6.9h-3.8c.2-3.3 1-5.6 1.9-6.9zM9.4 5.4A15 15 0 0 0 8.1 11h-3a8 8 0 0 1 4.3-5.6zM5.1 13h3a15 15 0 0 0 1.3 5.6A8 8 0 0 1 5.1 13zm6.9 6.9c-.9-1.3-1.7-3.6-1.9-6.9h3.8c-.2 3.3-1 5.6-1.9 6.9zm2.6-1.3a15 15 0 0 0 1.3-5.6h3a8 8 0 0 1-4.3 5.6z"/></svg>
        www.vextra.com
      </li>
    </ul>
    <div class="address">Door No. Street Name<br>City Name, State, Zip Code</div>
  </section>

  <section class="card card-back" aria-label="Brand side of business card">
    <div class="faint-square"></div>
    <div class="back-name">VEXTRA</div>
    <div class="back-web">www.vextra.com</div>
  </section>

</body>
</html>
```